Business Card Design

Online clothing womens clothing store, I sell my clothing online and at the markets.

i would like the attached picture on the front of the card and the contact information on the back.

Industry/Entity Type

Business

Contact Information for Business Card

Marlow Thread
Karen Whitfield
(Instagram symbol) _marlow_thread_
(Facebook symbol) www.fakebookexample.com/marlowthreadau/

W : www.marlowthread.example.au
E : info@marlowthread.example.au
P : 0498716204

```html
<!DOCTYPE html>
<html lang="en">
<head>
<meta charset="utf-8">
<title>Marlow Thread — Business Card</title>
<link href="https://fonts.googleapis.com/css2?family=Open+Sans:wght@300;400;600&display=swap" rel="stylesheet">
<style>
  :root {
    --page: #ece9e4;
    --band-blue: #1f2d8f;
    --ink-black: #121212;
    --paper-white: #ffffff;
    --text-light: #e8e8e8;
    --logo-ink: #2a2a2a;
    --rule: #cfcfcf;
    --photo-sky: #c9cdd2;
    --photo-grass: #6f7f52;
    --photo-bench: #d9d6d0;
    --mist-light: #e4e8e8;
    --mist-teal: #7f9a98;
    --mist-dark: #3f4a50;
  }
  * { box-sizing: border-box; margin: 0; padding: 0; }
  html, body { width: 1200px; height: 858px; overflow: hidden; }
  body {
    background: var(--page);
    font-family: "Open Sans", Arial, sans-serif;
    position: relative;
  }
  .card {
    position: absolute;
    top: 269px;
    width: 560px;
    height: 320px;
    overflow: hidden;
    box-shadow: 0 6px 18px rgba(0,0,0,0.18);
  }
  .card--contact { left: 26px; background: var(--ink-black); }
  .card--front { left: 614px; }

  /* contact side */
  .blue-band {
    position: absolute; left: 0; width: 100%; height: 12px;
    background: var(--band-blue);
  }
  .blue-band--top { top: 0; }
  .blue-band--bottom { bottom: 0; }
  .photo-strip {
    position: absolute; top: 12px; left: 0; width: 100%; height: 138px;
  }
  .photo { position: absolute; top: 0; height: 100%; }
  .photo--bench {
    left: 0; width: 50%;
    background: linear-gradient(160deg, var(--photo-sky) 0%, var(--photo-bench) 45%, #b89a86 75%, #8d7a6a 100%);
  }
  .photo--field {
    right: 0; width: 50%;
    background: linear-gradient(180deg, #b8bec6 0%, var(--photo-sky) 52%, var(--photo-grass) 70%, #556243 100%);
  }
  .logo-box {
    position: absolute; top: 46px; left: 168px; width: 224px; height: 46px;
    background: rgba(255,255,255,0.55);
    display: flex; align-items: center; justify-content: center;
  }
  .logo-name {
    font-weight: 400; font-size: 15px; letter-spacing: 4px;
    color: var(--logo-ink); text-transform: uppercase;
  }
  .info-band {
    position: absolute; top: 150px; left: 0; width: 100%; height: 158px;
    display: flex; align-items: center;
  }
  .holder-name {
    width: 210px; flex: none; text-align: center;
    font-weight: 300; font-size: 26px; color: var(--text-light);
  }
  .divider {
    width: 2px; height: 112px; flex: none; background: var(--rule);
  }
  .contact-list {
    list-style: none; padding: 0 20px 0 18px; min-width: 0;
    display: flex; flex-direction: column; gap: 7px;
  }
  .contact-item {
    display: flex; align-items: center; gap: 10px;
    font-size: 13px; color: var(--text-light); white-space: nowrap;
  }
  .contact-icon {
    width: 15px; height: 15px; flex: none;
    background: var(--paper-white); border-radius: 2px;
    display: flex; align-items: center; justify-content: center;
  }
  .contact-icon--plain { background: none; border: 1.5px solid var(--paper-white); }

  /* front side */
  .mist-photo {
    position: absolute; inset: 0;
    background:
      radial-gradient(ellipse at 40% 75%, var(--mist-dark) 0%, rgba(63,74,80,0.6) 30%, transparent 60%),
      linear-gradient(160deg, var(--mist-light) 0%, #c8d2d3 40%, var(--mist-teal) 70%, var(--mist-dark) 100%);
  }
  .front-name {
    position: absolute; left: 40px; right: 40px; top: 126px;
    text-align: center;
    font-weight: 600; font-size: 46px; letter-spacing: 3px;
    color: var(--paper-white); text-transform: uppercase;
  }
</style>
</head>
<body>

<section class="card card--contact" aria-label="Business card, contact side">
  <div class="blue-band blue-band--top"></div>
  <div class="photo-strip">
    <div class="photo photo--bench" role="img" aria-label="Photo of two women in boho clothing sitting on a wooden bench"></div>
    <div class="photo photo--field" role="img" aria-label="Photo of a woman in a long dress standing in a grassy field under a cloudy sky"></div>
    <div class="logo-box"><span class="logo-name">Marlow Thread</span></div>
  </div>
  <div class="info-band">
    <p class="holder-name">Karen Whitfield</p>
    <div class="divider"></div>
    <ul class="contact-list">
      <li class="contact-item">
        <span class="contact-icon">
          <svg width="10" height="10" viewBox="0 0 10 10"><path d="M2 1 L4 1 L4.6 3 L3.5 4 Q4.5 6 6 6.5 L7 5.4 L9 6 L9 8 Q5 9 2.5 6.5 Q1 4.5 2 1Z" fill="#121212"/></svg>
        </span>0498716204
      </li>
      <li class="contact-item">
        <span class="contact-icon">
          <svg width="11" height="9" viewBox="0 0 11 9"><rect x="0.5" y="0.5" width="10" height="8" fill="none" stroke="#121212"/><path d="M0.5 0.5 L5.5 5 L10.5 0.5" fill="none" stroke="#121212"/></svg>
        </span>info@marlowthread.example.au
      </li>
      <li class="contact-item">
        <span class="contact-icon">
          <svg width="10" height="10" viewBox="0 0 10 10"><circle cx="5" cy="5" r="4" fill="none" stroke="#121212"/><path d="M1 5 H9 M5 1 Q2.5 5 5 9 M5 1 Q7.5 5 5 9" fill="none" stroke="#121212" stroke-width="0.8"/></svg>
        </span>www.marlowthread.example.au
      </li>
      <li class="contact-item"><span class="contact-icon contact-icon--plain"></span>_marlow_thread_</li>
      <li class="contact-item"><span class="contact-icon"></span>www.fakebookexample.com/marlowthreadau/</li>
    </ul>
  </div>
  <div class="blue-band blue-band--bottom"></div>
</section>

<section class="card card--front" aria-label="Business card, front side">
  <div class="mist-photo" role="img" aria-label="Misty photo of a rocky hillside fading into pale fog"></div>
  <p class="front-name">Marlow Thread</p>
</section>

</body>
</html>
```